We need a complete design for our construction company KELTO CONSTRUCTION based in Auckland New Zealand, we need a logo, website, business card, vehicle design etc..
We are a mid to high-end construction company who work mostly on residential projects and some commercial.

What we want to see in the design;
Professional,
Architectural,
Simple,
Alternative,

We want the design to communicate professionalism, high quality wormanship and and quality service.

Target Market(s)

People looking for a quality building/ construction company

Industry/Entity Type

Construction Company

Contact Information for Business Card

KELTO CONSTRUCTION.co.nz
Lino Verasek
lino@keltoconstruction.example.nz
021 5807 462

Logo Text

KELTO CONSTRUCTION

Number of Pages Required

5+ page

Font styles to use
Sans Serif

Colors

Designer to choose colors to be used in the design.

Requirements
Must have
• Must appear high end, professional, quality, be simple, easy to use, give security to potential clients
Nice to have
• high-quality photos of our recent projects
• about us page
• blog page
• contact us page
• high quality content
Should not have
• should not be hard to use and have too much going on.

```html
<!DOCTYPE html>
<html lang="en">
<head>
<meta charset="utf-8">
<title>Kelto Construction</title>
<link rel="stylesheet" href="https://fonts.googleapis.com/css2?family=Poppins:ital,wght@0,300;0,400;0,500;0,600;1,400&display=swap">
<style>
:root{
  --orange:#eea11b;
  --orange-deep:#e59412;
  --ink:#222222;
  --body:#333333;
  --footer:#2b2a29;
  --footer-line:#46443f;
  --footer-text:#a9a7a2;
  --white:#ffffff;
}
*{box-sizing:border-box;margin:0;padding:0}
html,body{width:1200px;height:2875px;overflow:hidden}
body{font-family:"Poppins",sans-serif;color:var(--body);background:var(--white);position:relative}
.abs{position:absolute}
a{color:inherit;text-decoration:none}

/* Header / hero */
.hero{left:0;top:0;width:1200px;height:537px;background:linear-gradient(160deg,#3c3c3e 0%,#2e2a28 45%,#4a3a2c 75%,#2a2624 100%)}
.hero-shade{left:0;top:0;width:1200px;height:537px;background:linear-gradient(180deg,rgba(0,0,0,.35),rgba(0,0,0,.15) 60%,rgba(0,0,0,.3))}
.brand{display:flex;align-items:center;gap:8px;font-weight:600;font-size:13px;letter-spacing:.3px}
.brand-mark{width:14px;height:14px;background:var(--orange)}
.site-brand{left:161px;top:52px;color:var(--white)}
.nav{left:466px;top:44px;display:flex;gap:0;font-size:13px;color:var(--white)}
.nav a{position:absolute;white-space:nowrap}
.nav .active{color:var(--orange)}
.call{left:899px;top:32px;text-align:right;color:var(--white)}
.call small{display:block;font-size:10px;margin-right:0}
.call strong{display:block;font-size:18px;font-weight:600;color:var(--orange);line-height:1.2}
.call-icon{left:1013px;top:40px;width:26px;height:26px;border-radius:50%;background:var(--orange);display:flex;align-items:center;justify-content:center}
.hero-place{left:0;top:236px;width:1200px;text-align:center;color:var(--white);font-size:17px;letter-spacing:2px}
.hero-title{left:0;top:270px;width:1200px;text-align:center;color:var(--white);font-size:28px;font-weight:500;letter-spacing:3px}
.btn{display:inline-flex;align-items:center;justify-content:center;background:var(--orange);color:var(--white);border-radius:24px;font-weight:500}
.hero-btn{left:506px;top:326px;width:188px;height:46px;font-size:13px}
.dots{left:511px;top:498px;display:flex;gap:10px}
.dots span{width:42px;height:4px;background:var(--white)}
.dots span.off{background:rgba(255,255,255,.35)}

/* Welcome */
.welcome-title{left:0;top:572px;width:1200px;text-align:center;font-size:31px;font-weight:500;color:var(--ink)}
.welcome-text{left:210px;top:626px;width:780px;text-align:center;font-size:11px;line-height:22px}
.service{top:711px;width:276px}
.service-img{width:276px;height:155px}
.service h3{margin-top:17px;font-size:14px;font-weight:400;color:var(--orange);display:flex;align-items:center;gap:10px}
.service p{margin-top:15px;font-size:11px;line-height:19px}

/* Projects */
.projects-band{left:0;top:1035px;width:1200px;height:217px;background:var(--orange);color:var(--white);text-align:center}
.projects-band h2{margin-top:40px;font-size:31px;font-weight:400}
.projects-band p{margin:14px auto 0;width:560px;font-size:11px;line-height:21px}
.filters{margin-top:14px;display:flex;justify-content:center;gap:22px;font-size:12px}
.filters span{padding:3px 16px;border-radius:12px}
.filters .on{background:var(--white);color:var(--orange)}
.tile{position:absolute}
.tile-caption{left:34px;bottom:32px;color:var(--white)}
.tile-caption h4{font-size:17px;font-weight:500;letter-spacing:1.5px}
.tile-caption p{font-size:11px;margin-top:4px}

/* Why */
.why-title{left:161px;top:1912px;font-size:31px;font-weight:500;color:var(--ink)}
.why-text{left:161px;top:1974px;width:360px;font-size:11px;line-height:21.5px}
.why-btn{left:161px;top:2139px;width:108px;height:34px;font-size:12px}
.why-art{left:521px;top:1879px;width:529px;height:316px;border-radius:4px;background:radial-gradient(ellipse at 50% 55%,#c98a5a 0%,#e2c7a2 35%,#f3ece2 62%,#ffffff 80%)}

/* Testimonials */
.testimonials{left:0;top:2247px;width:1200px;height:295px;background:var(--orange);color:var(--white)}
.testimonials h2{position:absolute;top:50px;width:1200px;text-align:center;font-size:31px;font-weight:400}
.quote{left:186px;top:131px;width:594px;text-align:center;font-size:12px;font-style:italic;line-height:24.5px}
.avatar{left:811px;top:122px;width:100px;height:100px;border-radius:50%;background:linear-gradient(160deg,#d7d3cd,#8e8680);border:3px solid rgba(255,255,255,.6)}
.client{left:932px;top:147px;font-size:13px;font-weight:500;line-height:24px}
.arrow-l{left:86px;top:160px}
.arrow-r{left:1062px;top:160px}

/* Footer */
.footer{left:0;top:2542px;width:1200px;height:333px;background:var(--footer);color:var(--footer-text)}
.fcol{position:absolute;top:63px;font-size:12px}
.fcol h5{color:var(--white);font-size:15px;font-weight:500;margin-bottom:13px}
.fcol li{list-style:none;line-height:26px}
.socials{display:flex;gap:14px;align-items:center;margin-bottom:20px}
.social-dot{width:18px;height:18px;background:var(--white);border-radius:3px}
.fline{left:161px;top:259px;width:878px;height:1px;background:var(--footer-line)}
.footer-brand{left:161px;top:283px;color:var(--white);font-size:11px}
.copyright{left:620px;top:284px;width:417px;text-align:right;font-size:11px;color:var(--white)}
</style>
</head>
<body>

<header>
  <div class="abs hero" role="img" aria-label="Photo of a brick house under construction with exposed timber framing at dusk"></div>
  <div class="abs hero-shade"></div>
  <div class="abs brand site-brand"><span class="brand-mark"></span>KELTO CONSTRUCTION</div>
  <nav class="abs nav">
    <a class="active" style="left:0">Home</a>
    <a style="left:73px">About us</a>
    <a style="left:165px">Projects</a>
    <a style="left:251px">Blog</a>
    <a style="left:314px">Contact Us</a>
  </nav>
  <div class="abs call"><small>Call Us</small><strong>442 555 0187</strong></div>
  <div class="abs call-icon">
    <svg width="13" height="13" viewBox="0 0 24 24"><path fill="#fff" d="M6.6 10.8a15 15 0 0 0 6.6 6.6l2.2-2.2c.3-.3.7-.4 1-.2 1.1.4 2.3.6 3.6.6.6 0 1 .4 1 1V20c0 .6-.4 1-1 1A17 17 0 0 1 3 4c0-.6.4-1 1-1h3.5c.6 0 1 .4 1 1 0 1.3.2 2.5.6 3.6.1.3 0 .7-.2 1z"/></svg>
  </div>
  <p class="abs hero-place">Auckland, NewZealand</p>
  <h1 class="abs hero-title">Kelto Construction Company</h1>
  <a class="abs btn hero-btn">CONTACT US TODAY</a>
  <div class="abs dots"><span></span><span></span><span class="off"></span><span></span></div>
</header>

<section>
  <h2 class="abs welcome-title">Welcome to Kelto Construction</h2>
  <p class="abs welcome-text">Sed ut perspiciatis unde omnis iste natus error sit voluptatem accusantium doloremque laudantium, totam rem aperiam, eaque ipsa quae ab illo inventore veritatis et quasi architecto beatae vitae dicta sunt explicabo.mo enim ipsam voluptatem quia voluptas sit aspernatur aut</p>

  <article class="abs service" style="left:161px">
    <div class="service-img" role="img" aria-label="Photo of a timber attic interior under renovation" style="background:linear-gradient(135deg,#8a5a3a,#d9c2a4 50%,#a36a45)"></div>
    <h3>Residential Construction <svg width="16" height="8" viewBox="0 0 16 8"><path d="M0 4h14M11 1l3 3-3 3" stroke="#333" fill="none"/></svg></h3>
    <p>Sed ut perspiciatis unde omnis iste natus errorit voluptatem accusantium doloremque laudantium, totam rem aperiam, eaque isaa.</p>
  </article>
  <article class="abs service" style="left:461px">
    <div class="service-img" role="img" aria-label="Photo of a commercial building site with tower cranes" style="background:linear-gradient(180deg,#7fa0b0,#b8c4c2 45%,#b0562e 75%,#6e4a34)"></div>
    <h3>Commercial Construction <svg width="16" height="8" viewBox="0 0 16 8"><path d="M0 4h14M11 1l3 3-3 3" stroke="#333" fill="none"/></svg></h3>
    <p>Sed ut perspiciatis unde omnis iste natus errorit voluptatem accusantium doloremque laudantium, totam rem aperiam, eaque isaa.</p>
  </article>
  <article class="abs service" style="left:761px">
    <div class="service-img" role="img" aria-label="Photo of two builders reviewing building plans" style="background:linear-gradient(135deg,#c9a7a0,#3a3a3c 45%,#e9e4dc 75%,#b58f7a)"></div>
    <h3>About Us <svg width="16" height="8" viewBox="0 0 16 8"><path d="M0 4h14M11 1l3 3-3 3" stroke="#333" fill="none"/></svg></h3>
    <p>Sed ut perspiciatis unde omnis iste natus errorit voluptatem accusantium doloremque laudantium, totam rem aperiam, eaque isaa.</p>
  </article>
</section>

<section>
  <div class="abs projects-band">
    <h2>Our Recent Projects</h2>
    <p>Sed ut perspiciatis unde omnis iste natus error sit voluptatem accusantium doloremque laudtam rem aperiam, eaque ipsa quae ab illo inventore veritatis et quasi architecto bea.</p>
    <div class="filters"><span class="on">All</span><span>Residential</span><span>Commercial</span></div>
  </div>
  <div class="tile" style="left:0;top:1256px;width:596px;height:283px;background:linear-gradient(160deg,#7a8a6a,#d8d2c6 45%,#c98a4a 70%,#4a4a3c)" role="img" aria-label="Photo of a modern two-storey house with large glass windows"></div>
  <div class="tile" style="left:604px;top:1256px;width:291px;height:283px;background:linear-gradient(180deg,#4f86c4,#dde2e0 45%,#7a8a6a)" role="img" aria-label="Photo of a white commercial office building with palm trees"></div>
  <div class="tile" style="left:903px;top:1256px;width:297px;height:283px;background:linear-gradient(180deg,#9a9088,#ddd8d0 55%,#5a3a26)" role="img" aria-label="Photo of a house interior with staircase and timber floor"></div>
  <div class="tile" style="left:0;top:1547px;width:295px;height:282px;background:linear-gradient(180deg,#6b8c4a,#8a6050 45%,#7aa04a)" role="img" aria-label="Photo of a brick family home with green lawn"></div>
  <div class="tile" style="left:303px;top:1547px;width:293px;height:282px;background:linear-gradient(160deg,#3f6fb0,#d8b88a 45%,#8a5a3a)" role="img" aria-label="Photo of a rendered commercial building corner"></div>
  <div class="tile" style="left:604px;top:1547px;width:596px;height:282px;background:linear-gradient(160deg,#6a7a6a,#5a5550 50%,#2a2a28)" role="img" aria-label="Photo of a contemporary timber and render home">
    <div class="abs tile-caption"><h4>SED UTPERSPICIATISUND</h4><p>Sed ut perspiciatis unde omnis iste natus error sit voluptatem</p></div>
  </div>
</section>

<section>
  <h2 class="abs why-title">Why Choose Us?</h2>
  <p class="abs why-text">Sed ut perspiciatis unde omnis iste natus error sit voluptatem accusantium doloremque laudantium, totam rem aperiam, ea que ipsa quae ab illo inventore veritatis et quasi architecto beatae vitae dicta sunt explicabo.mo enim ipsam voluptatem quia volu ptas sit aspernatur autvitae dicta sunt explicabo.mo enim ipsam voluptatem quia voluptas sit aspernatur autvitae dicta sunt explicabo.mo enim ipsam voluptatem quia volu.</p>
  <a class="abs btn why-btn">Read More</a>
  <div class="abs why-art" role="img" aria-label="Illustration of a cutaway house with timber roof frame on building plans"></div>
</section>

<section class="abs testimonials">
  <h2>Client Testimonials</h2>
  <svg class="abs arrow-l" width="40" height="14" viewBox="0 0 40 14"><path d="M40 7H2M8 1L2 7l6 6" stroke="#fff" stroke-width="2" fill="none"/></svg>
  <p class="abs quote">Lorem ipsum dolor sit amet, consectetur adipiscing elit, sed do eiusmod tempor incididunt ut labore dolore magna aliqua. Ut enim ad minim veniam.Lorem ipsum dolor sit amet, consectetur adipiscing elied do eiusmod tempor incididunt ut labore et dolore magna aliqua. Ut enim ad minim veniam.</p>
  <div class="abs avatar" role="img" aria-label="Portrait photo of the client"></div>
  <p class="abs client">Marek Tolvan<br>City Name</p>
  <svg class="abs arrow-r" width="40" height="14" viewBox="0 0 40 14"><path d="M0 7h38M32 1l6 6-6 6" stroke="#fff" stroke-width="2" fill="none"/></svg>
</section>

<footer class="abs footer">
  <div class="fcol" style="left:161px"><h5>About</h5><ul><li>Sed uerspiciatiem</li><li>Comnisteatusit</li><li>Sed uerspiciatiem</li><li>Comnisteatusit</li><li>Perspiciatis unde</li></ul></div>
  <div class="fcol" style="left:349px"><h5>Nav Links</h5><ul><li>Home</li><li>About us</li><li>Projects</li><li>Blog</li><li>Contact Us</li></ul></div>
  <div class="fcol" style="left:514px"><h5>Projects</h5><ul><li>Sed uerspiciatiem</li><li>Comnisteatusit</li><li>Sed uerspiciatiem</li><li>Comnisteatusit</li><li>Perspiciatis unde</li></ul></div>
  <div class="fcol" style="left:709px"><h5>Connect</h5>
    <div class="socials">
      <svg width="22" height="16" viewBox="0 0 22 16" aria-label="Email"><rect x="1" y="1" width="20" height="14" fill="none" stroke="#fff" stroke-width="2"/><path d="M1 1l10 8 10-8" stroke="#fff" stroke-width="2" fill="none"/></svg>
      <span class="social-dot" aria-label="Social link"></span>
      <span class="social-dot" aria-label="Social link"></span>
      <span class="social-dot" aria-label="Social link"></span>
    </div>
    <h5>Policies</h5><ul><li>Privacy</li><li>Complaint and Feedback</li></ul></div>
  <div class="fcol" style="left:926px"><h5>Other Links</h5><ul><li>Sed uerspiciatis</li><li>Sed uerspiciatiem</li><li>Comnisteatusit</li><li>Perspiciatis unde</li><li>Sed uerspiciatiem</li></ul></div>
  <div class="abs fline"></div>
  <div class="abs brand footer-brand"><span class="brand-mark"></span>KELTO CONSTRUCTION</div>
  <p class="abs copyright">© 2018 Kelto Construction. Privacy Policy | Terms of Use | Contact</p>
</footer>

</body>
</html>
```